New Business Card Design Project LORVANTI-Italy

we are LORVANTI-Italy
our company in the market for 3 years we are luxury cosmetic company and its about time for a facelift :)
i will like to have elegant luxurious and unique business card
that will give the person that get it a unique, luxurious and elegant impression
I'm VERY OPEN FOR NEW IDEAS , even duo i add a few files of things that i see on line and i like them

i add my logo as well
my website is LORVANTI.COM
(if you would like to see the main style that we have)

Target Market(s)

adult that have money :)

Industry/Entity Type

Business

Contact Information for Business Card

Name - Dario Lorvanti
Position - CEO and CO Founder
address - 4817 E Halvern
telephone - 555-384-1926
email - dario@lorvanti.com
fax - 555-384-1926
website - LORVANTI.COM

Colors
000000
959595
fbee3e
ffffff

Requirements
Must have
• big logo in GOLD color
• elegant look
• impressive
Nice to have
• not must but maybe classy pattern background
• not must but maybe emblem
• maybe clear plastic business card
Should not have
• colors
• images

```html
<!DOCTYPE html>
<html lang="en">
<head>
<meta charset="utf-8">
<title>Lorvanti Italy – Business Card</title>
<link rel="stylesheet" href="https://fonts.googleapis.com/css2?family=Cinzel:wght@400&family=Roboto:wght@400&display=swap">
<style>
  :root {
    --backdrop: #d9d2c6;
    --card-black: #1c1c1c;
    --card-black-edge: #101010;
    --card-clear: #f1efeb;
    --gold: #b8913a;
    --gold-dark: #9a7420;
    --ink: #1a1a1a;
  }
  * { margin: 0; padding: 0; box-sizing: border-box; }
  html, body {
    width: 1200px;
    height: 970px;
    overflow: hidden;
    background: var(--backdrop);
  }
  .business-card {
    position: absolute;
    left: 177px;
    top: 244px;
    width: 846px;
    height: 482px;
    border-radius: 22px;
    overflow: hidden;
    display: flex;
    box-shadow: 0 6px 24px rgba(0,0,0,0.18);
  }
  .brand-panel {
    position: relative;
    width: 423px;
    height: 100%;
  }
  .brand-texture {
    position: absolute;
    inset: 0;
    background: radial-gradient(circle at 50% 38%, #2e2e2e 0%, var(--card-black) 45%, var(--card-black-edge) 100%);
  }
  .brand-emblem {
    position: absolute;
    left: 140px;
    top: 106px;
    width: 136px;
    height: 136px;
    border: 3px solid var(--gold);
    border-radius: 50%;
  }
  .brand-name,
  .brand-origin {
    position: absolute;
    left: 0;
    width: 100%;
    text-align: center;
    font-family: "Cinzel", serif;
    font-weight: 400;
    color: var(--gold);
  }
  .brand-name {
    top: 272px;
    font-size: 52px;
    letter-spacing: 1px;
  }
  .brand-origin {
    top: 356px;
    font-size: 20px;
    letter-spacing: 1px;
  }
  .contact-panel {
    position: relative;
    flex: 1;
    background: linear-gradient(160deg, #f6f4f0 0%, var(--card-clear) 55%, #e6ebef 100%);
  }
  .holder-name {
    position: absolute;
    left: 47px;
    top: 96px;
    font-family: "Cinzel", serif;
    font-weight: 400;
    font-size: 36px;
    letter-spacing: 1px;
    color: var(--gold-dark);
    white-space: nowrap;
  }
  .holder-role {
    position: absolute;
    left: 47px;
    top: 136px;
    font-family: "Roboto", sans-serif;
    font-size: 21px;
    color: var(--ink);
  }
  .contact-list {
    position: absolute;
    left: 47px;
    top: 222px;
    list-style: none;
    font-family: "Roboto", sans-serif;
    font-size: 20px;
    line-height: 33.5px;
    color: var(--ink);
  }
</style>
</head>
<body>
  <div class="business-card">
    <section class="brand-panel">
      <div class="brand-texture" role="img" aria-label="Subtle dark ornamental pattern background"></div>
      <div class="brand-emblem"></div>
      <div class="brand-name">LORVANTI</div>
      <div class="brand-origin">ITALY</div>
    </section>
    <section class="contact-panel">
      <h1 class="holder-name">DARIO LORVANTI</h1>
      <p class="holder-role">CEO and CO Founder</p>
      <ul class="contact-list">
        <li>Tel. 555-384-1926</li>
        <li>Fax. 555-384-1926</li>
        <li>dario@lorvanti.com</li>
        <li>www.lorvanti.com</li>
        <li>Address. 4817 E Halvern</li>
      </ul>
    </section>
  </div>
</body>
</html>
```